Website Redesign using existing images, copy etc.

I'm looking for a website redesign/refresh of my current WordPress website. I would like to utilize the same photography, a new photo viewer, and an overall refresh of the entire design. This will need to be WordPress with simple accessibility to make changes as we add additional properties and make updates. We auction luxury real estate and luxury yachts for non-distressed sellers. It needs to be simple, luxurious and with ease of use for both web and especially mobile. www.BrindleHarrow.com

```html
<!DOCTYPE html>
<html lang="en">
<head>
<meta charset="utf-8">
<title>Brindle Harrow — Real Estate &amp; Yachts</title>
<link rel="stylesheet" href="https://fonts.googleapis.com/css2?family=Libre+Baskerville:wght@400;700&family=Arimo:wght@400;700&display=swap">
<style>
:root{
  --olive:#8f8a66;
  --olive-dark:#7d7856;
  --sand:#ebe8e1;
  --ink:#3a3a3a;
  --muted:#666;
  --footer:#4b4b4b;
  --white:#fff;
  --serif:"Libre Baskerville", Georgia, serif;
  --sans:"Arimo", Arial, sans-serif;
}
*{box-sizing:border-box;margin:0;padding:0}
html,body{width:1200px;height:3876px;overflow:hidden}
body{position:relative;background:var(--white);font-family:var(--sans);color:var(--ink)}
.abs{position:absolute}
.brand{font-family:var(--serif);font-size:24px;font-weight:400;letter-spacing:1px;color:var(--olive);white-space:nowrap}
.nav{left:588px;top:62px;display:flex;gap:30px;font-size:15px;font-weight:700;letter-spacing:.5px}
.phone-pill{left:920px;top:46px;width:168px;height:48px;border:2px solid var(--olive);border-radius:24px;display:flex;align-items:center;justify-content:center;gap:10px;font-size:15px;font-weight:700;box-shadow:0 4px 10px rgba(0,0,0,.12)}
.hero{left:0;top:137px;width:1200px;height:626px;background:linear-gradient(180deg,#8ea4b2 0%,#a9735c 40%,#6c5a45 75%,#3f4634 100%)}
.hero h1{position:absolute;left:0;top:226px;width:1200px;text-align:center;font-family:var(--serif);font-size:60px;color:var(--white);text-shadow:0 2px 6px rgba(0,0,0,.35)}
.rule{height:4px;background:var(--olive);width:55px;margin:0 auto}
.hero .rule{position:absolute;left:554px;top:296px;width:92px;background:var(--white)}
.btn{display:inline-flex;align-items:center;justify-content:center;border-radius:26px;font-size:15px;font-weight:700;letter-spacing:.3px;box-shadow:0 4px 10px rgba(0,0,0,.15)}
.btn-olive{background:var(--olive);color:var(--white)}
.btn-white{background:var(--white);color:var(--ink);border:2px solid var(--olive)}
.scroll{left:546px;top:708px;width:108px;height:108px;border-radius:50%;background:var(--white);border:2px solid var(--olive);display:flex;align-items:center;justify-content:center;box-shadow:0 6px 12px rgba(0,0,0,.1)}
.photo-ring{border-radius:50%;border:12px solid var(--olive);background:var(--white);padding:10px}
.photo-ring .photo{width:100%;height:100%;border-radius:50%}
.h2{font-family:var(--serif);font-size:35px;color:var(--ink);text-align:center}
.h2-left{font-family:var(--serif);font-size:27px;line-height:36px;color:var(--ink)}
.copy{font-size:14.5px;line-height:25px;color:var(--muted);text-align:justify}
.call-card{left:340px;top:1366px;width:328px;height:86px;background:var(--white);border-radius:43px;box-shadow:0 6px 16px rgba(0,0,0,.12);display:flex;align-items:center;gap:18px;padding-left:12px}
.call-card .ic{width:62px;height:62px;border-radius:50%;background:var(--olive);display:flex;align-items:center;justify-content:center}
.featured{left:0;top:1587px;width:1200px;height:425px;background:var(--sand)}
.press{display:flex;justify-content:center;gap:50px;position:absolute;top:222px;left:0;width:1200px}
.press span{display:block;width:100px;height:44px;background:#9a9a9a;border-radius:4px;opacity:.7}
.sold{left:0;top:2012px;width:1200px;height:369px;background:linear-gradient(180deg,#8f8a66,#807b59)}
.card{top:2166px;width:305px;height:410px;background:var(--white);box-shadow:0 4px 14px rgba(0,0,0,.12);text-align:center;padding:5px}
.card .photo{height:204px}
.card h3{font-size:17px;font-weight:400;margin-top:22px;letter-spacing:.3px}
.card p{font-size:14px;line-height:24px;color:var(--muted);margin:12px 16px 0}
.card .btn{margin-top:18px;width:124px;height:40px;font-size:13px}
.card.active{border-bottom:5px solid var(--olive)}
.arrow{top:2253px;width:36px;height:36px;border:2px solid var(--white);border-radius:50%;display:flex;align-items:center;justify-content:center}
.footer{left:0;top:3498px;width:1200px;height:378px;background:var(--footer);color:var(--white)}
.footer h4{font-size:17px;font-weight:700;letter-spacing:.3px;text-decoration:underline;text-underline-offset:6px}
.footer ul{list-style:none;margin-top:12px}
.footer li{font-size:14px;line-height:31px;display:flex;align-items:center;gap:18px}
.footer li::before{content:"";width:12px;height:12px;border-radius:50%;background:var(--olive)}
</style>
</head>
<body>

<header>
  <div class="abs brand" style="left:111px;top:56px;">BRINDLE HARROW</div>
  <nav class="abs nav"><span>BUY</span><span>SELL</span><span>ABOUT</span><span>CONTACT</span></nav>
  <div class="abs phone-pill">
    <svg width="14" height="14" viewBox="0 0 24 24"><path fill="#3a3a3a" d="M6.6 10.8a15 15 0 006.6 6.6l2.2-2.2c.3-.3.7-.4 1-.2 1.1.4 2.3.6 3.6.6.6 0 1 .4 1 1V20c0 .6-.4 1-1 1A17 17 0 013 4c0-.6.4-1 1-1h3.5c.6 0 1 .4 1 1 0 1.3.2 2.5.6 3.6.1.3 0 .7-.2 1z"/></svg>
    800-555-0142
  </div>
</header>

<section class="abs hero" role="img" aria-label="Aerial photograph of a brick waterfront estate at sunset">
  <h1>REAL ESTATE &amp; YACHTS</h1>
  <div class="rule"></div>
  <span class="abs btn btn-olive" style="left:333px;top:340px;width:260px;height:50px;">BROWSE UPCOMING AUCTIONS</span>
  <span class="abs btn btn-white" style="left:605px;top:340px;width:262px;height:50px;border-color:var(--white)">BROWSE PAST SUCCESSES</span>
</section>
<div class="abs scroll">
  <svg width="26" height="26" viewBox="0 0 24 24" fill="none" stroke="#8f8a66" stroke-width="2.4"><path d="M6 6l6 6 6-6M6 12l6 6 6-6"/></svg>
</div>

<section>
  <div class="abs photo-ring" style="left:111px;top:888px;width:532px;height:532px;">
    <div class="photo" role="img" aria-label="Interior of a luxury yacht salon with wood trim and cream sofas" style="background:radial-gradient(circle at 50% 40%,#f1e9dd,#b67a45 60%,#7a4a2a)"></div>
  </div>
  <div class="abs call-card">
    <div class="ic"><svg width="26" height="26" viewBox="0 0 24 24"><path fill="#fff" d="M6.6 10.8a15 15 0 006.6 6.6l2.2-2.2c.3-.3.7-.4 1-.2 1.1.4 2.3.6 3.6.6.6 0 1 .4 1 1V20c0 .6-.4 1-1 1A17 17 0 013 4c0-.6.4-1 1-1h3.5c.6 0 1 .4 1 1 0 1.3.2 2.5.6 3.6.1.3 0 .7-.2 1z"/></svg></div>
    <div>
      <div style="font-size:11px;font-weight:700;letter-spacing:.3px">REAL ESTATE &amp; YACHTS:</div>
      <div style="font-size:21px;color:var(--olive);margin-top:6px">CALL: <b>800-555-0142</b></div>
    </div>
  </div>
  <h2 class="abs h2-left" style="left:705px;top:980px;width:400px;">OVER ONE BILLION DOLLARS OF AUCTIONS MARKETED</h2>
  <div class="abs rule" style="left:705px;top:1092px;"></div>
  <p class="abs copy" style="left:705px;top:1122px;width:384px;">The experience of hearing the auctioneer’s final proclamation of “SOLD!” is unparalleled. Whether it’s the initial meeting with the seller at their estate or yacht, or the triumphant raising of the paddle by the winning buyer, we relish every moment of the process and the ensuing festivities. We’re confident that you will, too.</p>
  <span class="abs btn btn-olive" style="left:705px;top:1305px;width:152px;height:50px;">READ MORE</span>
</section>

<section class="abs featured">
  <h2 class="h2" style="margin-top:65px">AS FEATURED IN</h2>
  <div class="rule" style="margin-top:12px"></div>
  <p style="font-size:14.5px;line-height:25px;color:var(--muted);text-align:center;width:900px;margin:24px auto 0">By offering top-tier properties and vessels globally, along with strategic auction dates, exceptional marketing tactics, and a diligent public relations team, even the most prominent media outlets have taken notice. Check out some of our latest press features.</p>
  <div class="press"><span></span><span></span><span></span><span></span><span></span></div>
  <span class="abs btn btn-olive" style="left:524px;top:302px;width:152px;height:50px;">VIEW PRESS</span>
</section>

<section class="abs sold" role="img" aria-label="Faded waterfront estate photograph tinted olive">
  <h2 class="h2" style="margin-top:62px;color:var(--white)">SOLD BY BRINDLE HARROW</h2>
  <div class="rule" style="margin-top:12px;background:var(--white)"></div>
</section>
<div class="abs arrow" style="left:38px;"><svg width="14" height="14" viewBox="0 0 24 24" fill="none" stroke="#fff" stroke-width="3"><path d="M15 5l-7 7 7 7"/></svg></div>
<div class="abs arrow" style="left:1124px;"><svg width="14" height="14" viewBox="0 0 24 24" fill="none" stroke="#fff" stroke-width="3"><path d="M9 5l7 7-7 7"/></svg></div>

<article class="abs card" style="left:111px;">
  <div class="photo" role="img" aria-label="Bright living room with coastal furnishings" style="background:linear-gradient(160deg,#e8e4dc,#b8a48a)"></div>
  <h3>NAPLES I FLORIDA</h3>
  <p>Located in one of the most coveted communities in Naples, this extraordinary luxury property sold before auction.</p>
  <span class="btn btn-white">VIEW STORY</span>
</article>
<article class="abs card active" style="left:448px;">
  <div class="photo" role="img" aria-label="Multi-storey beach house with palm trees and pool" style="background:linear-gradient(180deg,#6aa1d8,#d9d0b8 55%,#6b9a45)"></div>
  <h3>SANIBEL I FLORIDA</h3>
  <p>Within days of just announcing the opportunity to the world, using our unique accelerated</p>
  <span class="btn btn-olive">VIEW STORY</span>
</article>
<article class="abs card" style="left:784px;">
  <div class="photo" role="img" aria-label="Navy-hulled motor yacht on the water" style="background:linear-gradient(180deg,#7fb1e3,#c8d6e4 45%,#1d2b4a 70%,#4a6f95)"></div>
  <h3>FORT LAUDERDALE I FLORIDA</h3>
  <p>This beautiful yacht got sold fast! Brindle Harrow deployed a full-throttle marketing blitz</p>
  <span class="btn btn-white">VIEW STORY</span>
</article>

<section>
  <h2 class="abs h2" style="left:0;top:2690px;width:1200px;">SUCCESS STORIES</h2>
  <div class="abs rule" style="left:572px;top:2750px;"></div>
  <p class="abs" style="left:160px;top:2768px;width:880px;font-size:14.5px;line-height:26px;color:var(--muted);text-align:center">Brindle Harrow is a top-tier destination for luxury property auctions, having overseen the auction marketing of numerous high-end estates and yachts. Our team of luxury home auction experts is committed to helping property owners obtain the best value for their assets while ensuring a timely sale.</p>
  <p class="abs copy" style="left:111px;top:2920px;width:414px;">Whether you have an expansive compound or a metropolitan penthouse, Brindle Harrow has the necessary skills and expertise to facilitate various luxury real estate auctions. What’s even better? Our team takes care of every aspect of the process in cooperation with tour realtor/broker, including property tours, photography and cinematography, marketing advertising, public relations and more.</p>
  <p class="abs copy" style="left:111px;top:3110px;width:414px;">Apart from high-end real estate auctions, we can also organize and execute luxury yacht auctions to help boat owners find qualified buyers for their vessels. Interested in finding out more about our luxury home and yacht auctions? Explore our current listings and success stories!</p>
  <span class="abs btn btn-olive" style="left:111px;top:3277px;width:140px;height:50px;">ABOUT US</span>
  <span class="abs btn btn-white" style="left:258px;top:3277px;width:216px;height:50px;">UPCOMING AUCTIONS</span>
  <div class="abs photo-ring" style="left:588px;top:2875px;width:500px;height:500px;">
    <div class="photo" role="img" aria-label="Stone manor house with pool patio at dusk" style="background:linear-gradient(180deg,#9bb4d6,#e4c7a8 40%,#8a7a68 65%,#c9b79f 85%,#4f7a3a)"></div>
  </div>
</section>

<footer class="abs footer">
  <div class="abs brand" style="left:111px;top:140px;color:var(--white);font-size:22px">BRINDLE HARROW</div>
  <div class="abs" style="left:198px;top:194px;display:flex;gap:6px">
    <span style="width:33px;height:33px;border-radius:50%;background:var(--olive)"></span>
    <span style="width:33px;height:33px;border-radius:50%;border:1.5px solid var(--white)"></span>
    <span style="width:33px;height:33px;border-radius:50%;border:1.5px solid var(--white)"></span>
    <span style="width:33px;height:33px;border-radius:50%;border:1.5px solid var(--white)"></span>
  </div>
  <div class="abs" style="left:476px;top:64px">
    <h4>COMPANY</h4>
    <ul><li>Home</li><li>Buy</li><li>Sell</li><li>About</li><li>Blog</li><li>Contact</li></ul>
  </div>
  <div class="abs" style="left:618px;top:64px">
    <h4>ABOUT</h4>
    <ul><li>Site Map</li><li>Terms Of Use</li><li>Privacy Policy</li><li>Cookie Policy</li><li>Disclaimer</li></ul>
  </div>
  <div class="abs" style="left:805px;top:64px">
    <h4>JOIN NEWSLETTER</h4>
    <div style="margin-top:22px;width:283px;height:46px;background:var(--white);border-radius:23px;display:flex;align-items:center;justify-content:space-between;padding:0 4px 0 18px">
      <span style="font-size:13px;color:#555">Email Address</span>
      <span class="btn btn-olive" style="width:100px;height:36px;font-size:14px;box-shadow:none">JOIN NOW</span>
    </div>
    <div style="margin-top:22px;width:60px;height:60px;border-radius:50%;border:3px solid var(--white)"></div>
  </div>
  <div class="abs" style="left:111px;top:330px;width:978px;height:1px;background:#5e5e5e"></div>
  <p class="abs" style="left:0;top:345px;width:1200px;text-align:center;font-size:12.5px">© 2023 BRINDLE HARROW &nbsp; I &nbsp; All Rights Reserved</p>
</footer>

</body>
</html>
```